Business Card, A4 Letter Head and DL Envelope for Brandvelle

We are looking for a design for our Business Card, A4 Letter Head and DL Envelope.

Brandvelle is a distributor of promotional products. We specialize in a range of branded promotional products, these include pens, polo shirts, key rings, drink bottles, uniforms and bags to name a few. We are experts in marketing and assist companies in choosing the right promotional product for their needs. We will predominately be an online business where customers visit our website and browse our range of promotional products and branding options.

Our colours are black, red, white and grey.

Files must be supplied in eps, pdf and ai format.

Please display the following information:
Derek Halloway
Account Manager
Suite xxx, 212 Ferrow Lane Melbourne, Victoria 3000
Phone +61 3 5550 1827
Mobile +61 455 016 342
sales@brandvelle-example.com.au
www.brandvelle-example.com.au

```html
<!DOCTYPE html>
<html lang="en">
<head>
<meta charset="utf-8">
<title>Brandvelle Letterhead</title>
<link rel="stylesheet" href="https://fonts.googleapis.com/css2?family=Arimo:wght@400;700&display=swap">
<style>
  :root {
    --ink: #1f1f1f;
    --charcoal: #2b2b2b;
    --brand-red: #d21f26;
    --brand-grey: #4a4a4a;
    --band-grey: #9c9c9c;
    --paper: #ffffff;
  }
  html, body {
    margin: 0;
    padding: 0;
    overflow: hidden;
    background: var(--paper);
  }
  .letterhead {
    position: relative;
    width: 869px;
    height: 1200px;
    overflow: hidden;
    background: var(--paper);
    font-family: "Arimo", Arial, sans-serif;
  }
  .header-swoosh,
  .footer-wave {
    position: absolute;
    left: 0;
    display: block;
  }
  .header-swoosh { top: 0; }
  .footer-wave { bottom: 0; }
  .brand {
    position: absolute;
    left: 52px;
    top: 32px;
    display: flex;
    align-items: center;
    gap: 10px;
  }
  .brand-dot {
    width: 50px;
    height: 50px;
    border-radius: 50%;
    background: var(--brand-red);
  }
  .brand-name {
    font-weight: 700;
    font-size: 22px;
    letter-spacing: 0.5px;
    color: var(--brand-grey);
    text-transform: uppercase;
  }
  .contact {
    position: absolute;
    left: 64px;
    right: 40px;
    color: var(--ink);
    white-space: nowrap;
  }
  .contact-address {
    top: 1131px;
    font-size: 22px;
    letter-spacing: 1.9px;
  }
  .contact-lines {
    top: 1159px;
    font-size: 18px;
    word-spacing: 0;
  }
  .contact-lines span + span { margin-left: 18px; }
</style>
</head>
<body>
  <div class="letterhead">
    <svg class="header-swoosh" width="340" height="80" viewBox="0 0 340 80" aria-hidden="true">
      <path d="M0 0 H335 Q150 18 0 68 Z" fill="var(--charcoal)"/>
      <path d="M335 0 Q150 18 0 68" fill="none" stroke="var(--brand-red)" stroke-width="2.5"/>
    </svg>

    <div class="brand">
      <span class="brand-dot"></span>
      <span class="brand-name">Brandvelle</span>
    </div>

    <svg class="footer-wave" width="869" height="180" viewBox="0 0 869 180" aria-hidden="true">
      <path d="M0 84 Q560 70 869 5 V180 H0 Z" fill="var(--band-grey)"/>
    </svg>

    <p class="contact contact-address">Suite xxx, 212 Ferrow Lane Melbourne, Victoria 3000</p>
    <p class="contact contact-lines">
      <span>T: +61 3 5550 1827</span>
      <span>E: sales@brandvelle-example.com.au</span>
      <span>www.brandvelle-example.com.au</span>
    </p>
  </div>
</body>
</html>
```